Create a memorable Web Design for real estate branding

we are a Minnepolis brokerage and boutique housing specialist with over 27 years of experience in the Global furnished housing industry, servicing the Greater Los Angeles area. Specializing in “warm environments” we offer a customized approach to satisfying our guests and client’s needs by offering a wide array of options in highly desirable areas. Additionally, Lantern Dwelling Partners offers assistance and expertise to home buyers, sellers and investors.

Industry/Entity Type

Real Estate

Number of Pages Required

1 page

Font styles to use
Serif
Sans Serif
Decorative

```html
<!DOCTYPE html>
<html lang="en">
<head>
<meta charset="utf-8">
<title>Lantern Dwelling Partners</title>
<link href="https://fonts.googleapis.com/css2?family=Roboto+Slab:wght@400;700&family=Open+Sans:wght@400;600;700&display=swap" rel="stylesheet">
<style>
:root{
  --teal:#0f9b83;
  --teal-dark:#0b7f6b;
  --lime:#8dc63f;
  --lime-dark:#76ad2c;
  --ink:#333840;
  --text:#3b3f45;
  --muted:#6a6f76;
  --pale:#e9ebef;
  --card-dark:#474c57;
  --card-light:#e6e8ec;
  --footer:#23272b;
  --footer-base:#1a1d20;
  --white:#ffffff;
}
*{box-sizing:border-box;margin:0;padding:0}
html,body{width:1200px;height:2782px;overflow:hidden}
body{font-family:"Open Sans",Arial,sans-serif;color:var(--text);background:var(--white);position:relative}

/* hero */
.hero{position:absolute;left:0;top:0;width:1200px;height:544px;background:linear-gradient(180deg,#3d5f86 0%,#8fa6bf 30%,#c9ccc9 55%,#6b7a62 80%,#2f3d34 100%)}
.hero-shade{position:absolute;inset:0;background:linear-gradient(180deg,rgba(0,0,0,.55) 0,rgba(0,0,0,.15) 70px,rgba(0,0,0,0) 200px)}
.topbar{position:absolute;top:0;left:117px;width:966px;height:33px;display:flex;align-items:center;justify-content:space-between;color:#fff;font-size:13px}
.topbar .right{display:flex;align-items:center;gap:8px}
.topbar .sep{width:1px;height:14px;background:#fff;margin:0 8px}
.dot-social{width:16px;height:16px;border-radius:50%;background:var(--teal)}
.brand{position:absolute;left:117px;top:33px;width:228px;height:67px;background:#fff;display:flex;align-items:center;justify-content:center;gap:8px}
.brand-mark{width:14px;height:14px;border-radius:50%;background:var(--lime)}
.brand-name{font-family:"Roboto Slab",Georgia,serif;font-weight:700;color:var(--teal);font-size:17px;line-height:1.1;text-align:left}
.nav{position:absolute;left:345px;top:33px;width:738px;height:67px;background:var(--lime);display:flex;align-items:center;justify-content:space-around;padding:0 10px}
.nav a{font-family:"Roboto Slab",Georgia,serif;font-size:13px;color:#fff;text-decoration:none;text-transform:uppercase;height:67px;line-height:67px;padding:0 14px}
.nav a.active{background:var(--lime-dark);box-shadow:inset 0 -3px 0 var(--teal)}
.tagline{position:absolute;left:117px;font-family:"Roboto Slab",Georgia,serif;font-weight:700;font-size:23px;color:#fff;background:var(--teal);padding:0 10px;height:40px;line-height:40px;text-transform:uppercase;letter-spacing:.3px}
.slide-dots{position:absolute;left:1036px;top:408px;display:flex;gap:6px}
.slide-dots span{width:10px;height:10px;background:rgba(255,255,255,.5)}
.slide-dots span.on{background:var(--teal)}
.search{position:absolute;left:117px;top:443px;width:966px;height:101px;background:rgba(30,34,38,.82)}
.search-label{position:absolute;left:18px;top:14px;font-family:"Roboto Slab",Georgia,serif;font-weight:700;color:var(--lime);font-size:15px;text-transform:uppercase}
.field{position:absolute;top:48px;height:30px;background:#fff;font-size:12px;color:#666;line-height:30px;padding-left:10px}
.field .caret{position:absolute;right:10px;top:13px;width:0;height:0;border-left:4px solid transparent;border-right:4px solid transparent;border-top:5px solid #999}
.search-btn{position:absolute;left:796px;top:48px;width:152px;height:30px;background:var(--lime);color:#fff;font-family:"Roboto Slab",Georgia,serif;font-weight:700;font-size:13px;text-align:center;line-height:30px}

/* shared */
.section-title{font-family:"Roboto Slab",Georgia,serif;color:var(--teal);text-align:center;text-transform:uppercase;font-size:24px}
.btn{display:flex;height:28px;width:117px}
.btn .lbl{flex:1;background:var(--teal);color:#fff;font-size:12px;text-align:center;line-height:28px}
.btn .arr{width:24px;background:var(--lime);display:flex;align-items:center;justify-content:center}

/* welcome */
.welcome{position:absolute;top:544px;left:0;width:1200px;height:283px;background:var(--pale)}
.welcome .pre{position:absolute;top:30px;width:100%;text-align:center;font-family:"Roboto Slab",Georgia,serif;font-size:15px;color:var(--ink)}
.welcome .section-title{position:absolute;top:50px;width:100%}
.welcome p{position:absolute;left:150px;top:104px;width:900px;text-align:center;font-size:12px;line-height:21px;color:var(--text)}
.welcome .btn{position:absolute;left:542px;top:220px}

/* recent */
.recent{position:absolute;top:827px;left:0;width:1200px;height:625px;background:#fff}
.recent .section-title{position:absolute;top:28px;width:100%}
.recent .intro{position:absolute;left:210px;top:68px;width:780px;text-align:center;font-size:12px;line-height:23px}
.grid{position:absolute;left:117px;top:158px;width:966px;height:410px;display:grid;grid-template-columns:repeat(4,1fr);grid-template-rows:repeat(2,1fr)}
.photo{width:100%;height:100%}
.card{padding:14px 18px;position:relative}
.card.dark{background:var(--card-dark);color:#fff}
.card.light{background:var(--card-light);color:var(--ink)}
.card h3{font-family:"Roboto Slab",Georgia,serif;font-weight:400;font-size:17px;margin-bottom:16px}
.card .price-row{display:flex;align-items:center;gap:16px;margin-bottom:16px}
.price{color:var(--lime);font-weight:700;font-size:14px}
.tag{background:#fff;color:var(--ink);font-size:10px;padding:3px 10px 3px 14px;clip-path:polygon(8px 0,100% 0,100% 100%,8px 100%,0 50%)}
.card.light .tag{background:var(--card-dark);color:#fff}
.feats{display:grid;grid-template-columns:1fr 1fr;row-gap:8px}
.feat{display:flex;gap:8px;align-items:flex-start}
.feat svg{margin-top:6px;flex:none}
.feat small{display:block;font-size:11px;opacity:.85}
.feat b{display:block;font-weight:400;font-size:16px;line-height:18px}
.feat b i{font-style:normal;font-size:10px}
.grid-arrow{position:absolute;top:1178px;width:26px;height:26px;background:#e5e7ea;display:flex;align-items:center;justify-content:center}

/* buyer / seller */
.info{position:absolute;top:1452px;width:600px;height:358px;color:#fff}
.info.buyer{left:0;background:linear-gradient(120deg,#0d8e77 0%,#0f9b83 60%,#12a58b 100%)}
.info.seller{left:600px;background:linear-gradient(120deg,#7fbd32 0%,#8dc63f 60%,#98ce4b 100%)}
.info h2{position:absolute;left:117px;top:46px;font-family:"Roboto Slab",Georgia,serif;font-weight:400;font-size:25px;text-transform:uppercase}
.info.seller h2,.info.seller .copy,.info.seller .btn{left:116px}
.info .copy{position:absolute;left:117px;top:96px;width:390px;font-size:12px;line-height:21px}
.info .copy p+p{margin-top:8px}
.info .btn{position:absolute;left:117px;top:283px}
.info.buyer .btn .lbl{background:var(--teal-dark)}

/* testimonials */
.clients{position:absolute;top:1810px;left:0;width:1200px;height:282px;background:var(--pale)}
.clients .section-title{position:absolute;top:33px;width:100%}
.avatar{position:absolute;left:162px;top:114px;width:96px;height:96px;border-radius:50%;background:radial-gradient(circle at 50% 40%,#cfb9a6 0,#9a8a80 55%,#d9dde2 100%);border:3px solid #fff}
.divider{position:absolute;left:297px;top:112px;width:1px;height:90px;background:#c7cbd1}
.quote-text{position:absolute;left:334px;top:110px;width:710px;font-size:12px;line-height:25px}
.client-name{position:absolute;left:334px;top:186px;font-family:"Roboto Slab",Georgia,serif;color:var(--teal);font-size:17px}
.qmark{position:absolute;font-family:"Roboto Slab",Georgia,serif;font-size:60px;color:#b9bdc4;line-height:1}
.dots{position:absolute;top:228px;left:577px;display:flex;gap:6px}
.dots span{width:11px;height:11px;border-radius:50%;background:#c2c6cc}
.dots span.on{background:var(--lime)}

/* news */
.news{position:absolute;top:2092px;left:0;width:1200px;height:381px;background:#fff}
.news .section-title{position:absolute;top:30px;width:100%}
.news .sub{position:absolute;top:68px;width:100%;text-align:center;font-size:12px}
.post{position:absolute;top:132px;width:463px;height:152px}
.post .thumb{position:absolute;left:0;top:0;width:150px;height:152px}
.post .body{position:absolute;left:171px;top:0;width:292px}
.post h4{font-family:"Roboto Slab",Georgia,serif;font-size:14px;line-height:21px;color:var(--ink)}
.post time{display:block;font-size:11px;color:var(--muted);margin:2px 0 8px}
.post p{font-size:11.5px;line-height:20px}
.post .more{display:flex;align-items:center;gap:6px;font-size:11px;margin-top:4px}
.news .btn{position:absolute;left:542px;top:318px}

/* footer */
.footer{position:absolute;top:2473px;left:0;width:1200px;height:257px;background:var(--footer);color:#c9ccd0}
.footer h5{font-family:"Roboto Slab",Georgia,serif;font-weight:400;color:var(--lime);font-size:16px;margin-bottom:18px}
.fcol{position:absolute;top:44px;font-size:11px;line-height:20px}
.fcol ul{list-style:none}
.email-box{width:170px;height:28px;background:#3a3f45;color:#ddd;font-size:11px;line-height:28px;padding-left:10px;margin-top:18px}
.submit{width:80px;height:28px;background:var(--lime);color:#fff;font-weight:700;font-size:11px;text-align:center;line-height:28px;margin-top:10px}
.map{position:absolute;left:792px;top:42px;width:291px;height:152px;background:linear-gradient(135deg,#e6ecd8 0%,#cfe0b2 45%,#b9d7e4 75%,#e8eaec 100%)}
.map-link{position:absolute;left:792px;top:200px;font-size:11px}
.base{position:absolute;top:2730px;left:0;width:1200px;height:52px;background:var(--footer-base);color:#bfc3c8;font-size:11px}
.base .links{position:absolute;left:117px;top:19px}
.base .copy{position:absolute;left:0;width:1200px;top:19px;text-align:center}
.base .social{position:absolute;right:117px;top:15px;display:flex;gap:10px}
.base .social span{width:20px;height:20px;border-radius:50%;background:#3d4248}
</style>
</head>
<body>

<header class="hero">
  <div class="hero-shade" role="img" aria-label="Photo of a modern white villa with pool and palm trees"></div>
  <div class="topbar">
    <span>Phone: (555) 014 2280</span>
    <span class="right">Email: hello@lanterndwelling.example<span class="sep"></span><span class="dot-social"></span><span class="dot-social"></span><span class="dot-social"></span><span class="dot-social"></span></span>
  </div>
  <div class="brand"><span class="brand-mark"></span><span class="brand-name">Lantern Dwelling<br>Partners</span></div>
  <nav class="nav">
    <a class="active">Home</a><a>About Us</a><a>Property</a><a>Buyer Info</a><a>Seller Info</a><a>News</a><a>Contact Us</a>
  </nav>
  <div class="tagline" style="top:254px">We are servicing the greater</div>
  <div class="tagline" style="top:299px">Los Angeles area</div>
  <div class="slide-dots"><span class="on"></span><span></span><span></span></div>
  <div class="search">
    <div class="search-label">Search Property
      <svg width="40" height="12" viewBox="0 0 40 12" style="vertical-align:middle"><path d="M2 3 Q20 12 36 7" stroke="#fff" fill="none" stroke-width="1"/><path d="M32 4 L37 7 L32 10" stroke="#fff" fill="none" stroke-width="1"/></svg>
    </div>
    <div class="field" style="left:18px;width:288px">Select Location<span class="caret"></span></div>
    <div class="field" style="left:328px;width:112px">Min Price</div>
    <div class="field" style="left:452px;width:114px">Max Price</div>
    <div class="field" style="left:581px;width:85px">Bed<span class="caret"></span></div>
    <div class="field" style="left:675px;width:85px">Bath<span class="caret"></span></div>
    <div class="search-btn">Property Search</div>
  </div>
</header>

<section class="welcome">
  <div class="pre">WELCOME TO</div>
  <h1 class="section-title">Lantern Dwelling Partners</h1>
  <p>Lorem Ipsum is simply dummy text of the printing and typesetting industry. Lorem Ipsum has been the industry's standard dummy text ever since the 1500s, when an unknown printer took a galley of type and scrambled it to make a type specimen book. It has survived not only five centuries, but also the leap into electronic typesetting, remaining essentially unchanged. It was popularised in the 1960s with the release of transfer sheets containing Lorem Ipsum passages, and more recently with desktop publishing software including versions of Lorem Ipsum.</p>
  <div class="btn"><span class="lbl">Learn More</span><span class="arr"><svg width="8" height="10"><path d="M2 1 L6 5 L2 9" stroke="#fff" stroke-width="2" fill="none"/></svg></span></div>
</section>

<section class="recent">
  <h2 class="section-title">Recent Property</h2>
  <p class="intro">Lorem Ipsum is simply dummy text of the printing and typesetting industry. Lorem Ipsum has been the industry's standard dummy text ever since the 1500s, when an unknown printer took a galley of type and scrambled it to make a type specimen book.</p>
  <div class="grid">
    <div class="photo" role="img" aria-label="Photo of a white modern house with garden" style="background:linear-gradient(160deg,#5b6f56,#d9dcd8 50%,#6f8d4a)"></div>
    <article class="card dark">
      <h3>Villa in Coral Gables</h3>
      <div class="price-row"><span class="price">$825,000</span><span class="tag">FOR SALE</span></div>
      <div class="feats">
        <div class="feat"><svg width="16" height="14"><rect x="1" y="1" width="14" height="12" fill="none" stroke="#0f9b83" stroke-width="2"/></svg><div><small>Area</small><b>3500<i>Sq Ft</i></b></div></div>
        <div class="feat"><svg width="16" height="14"><rect x="1" y="6" width="14" height="7" fill="#0f9b83"/><rect x="3" y="2" width="10" height="4" fill="#0f9b83"/></svg><div><small>Bedrooms</small><b>03</b></div></div>
        <div class="feat"><svg width="16" height="14"><rect x="1" y="6" width="14" height="5" rx="2" fill="none" stroke="#0f9b83" stroke-width="2"/></svg><div><small>Bathrooms</small><b>02</b></div></div>
        <div class="feat"><svg width="16" height="14"><path d="M1 6 L8 1 L15 6 V13 H1 Z" fill="#0f9b83"/></svg><div><small>Garages</small><b>01</b></div></div>
      </div>
    </article>
    <div class="photo" role="img" aria-label="Photo of a modern villa lit at dusk with pool" style="background:linear-gradient(180deg,#6d8fbf,#c8cdd6 50%,#2e3440)"></div>
    <article class="card light">
      <h3>Villa in Coral Gables</h3>
      <div class="price-row"><span class="price">$825,000</span><span class="tag">FOR SALE</span></div>
      <div class="feats">
        <div class="feat"><svg width="16" height="14"><rect x="1" y="1" width="14" height="12" fill="none" stroke="#0f9b83" stroke-width="2"/></svg><div><small>Area</small><b>3500<i>Sq Ft</i></b></div></div>
        <div class="feat"><svg width="16" height="14"><rect x="1" y="6" width="14" height="7" fill="#0f9b83"/><rect x="3" y="2" width="10" height="4" fill="#0f9b83"/></svg><div><small>Bedrooms</small><b>03</b></div></div>
        <div class="feat"><svg width="16" height="14"><rect x="1" y="6" width="14" height="5" rx="2" fill="none" stroke="#0f9b83" stroke-width="2"/></svg><div><small>Bathrooms</small><b>02</b></div></div>
        <div class="feat"><svg width="16" height="14"><path d="M1 6 L8 1 L15 6 V13 H1 Z" fill="#0f9b83"/></svg><div><small>Garages</small><b>01</b></div></div>
      </div>
    </article>
    <article class="card light">
      <h3>Villa in Coral Gables</h3>
      <div class="price-row"><span class="price">$825,000</span><span class="tag">FOR SALE</span></div>
      <div class="feats">
        <div class="feat"><svg width="16" height="14"><rect x="1" y="1" width="14" height="12" fill="none" stroke="#0f9b83" stroke-width="2"/></svg><div><small>Area</small><b>3500<i>Sq Ft</i></b></div></div>
        <div class="feat"><svg width="16" height="14"><rect x="1" y="6" width="14" height="7" fill="#0f9b83"/><rect x="3" y="2" width="10" height="4" fill="#0f9b83"/></svg><div><small>Bedrooms</small><b>03</b></div></div>
        <div class="feat"><svg width="16" height="14"><rect x="1" y="6" width="14" height="5" rx="2" fill="none" stroke="#0f9b83" stroke-width="2"/></svg><div><small>Bathrooms</small><b>02</b></div></div>
        <div class="feat"><svg width="16" height="14"><path d="M1 6 L8 1 L15 6 V13 H1 Z" fill="#0f9b83"/></svg><div><small>Garages</small><b>01</b></div></div>
      </div>
    </article>
    <div class="photo" role="img" aria-label="Photo of a two-storey family house with lawn" style="background:linear-gradient(180deg,#8fb2d6,#a9a49a 55%,#5f7f3c)"></div>
    <article class="card dark">
      <h3>Villa in Coral Gables</h3>
      <div class="price-row"><span class="price">$825,000</span><span class="tag">FOR SALE</span></div>
      <div class="feats">
        <div class="feat"><svg width="16" height="14"><rect x="1" y="1" width="14" height="12" fill="none" stroke="#0f9b83" stroke-width="2"/></svg><div><small>Area</small><b>3500<i>Sq Ft</i></b></div></div>
        <div class="feat"><svg width="16" height="14"><rect x="1" y="6" width="14" height="7" fill="#0f9b83"/><rect x="3" y="2" width="10" height="4" fill="#0f9b83"/></svg><div><small>Bedrooms</small><b>03</b></div></div>
        <div class="feat"><svg width="16" height="14"><rect x="1" y="6" width="14" height="5" rx="2" fill="none" stroke="#0f9b83" stroke-width="2"/></svg><div><small>Bathrooms</small><b>02</b></div></div>
        <div class="feat"><svg width="16" height="14"><path d="M1 6 L8 1 L15 6 V13 H1 Z" fill="#0f9b83"/></svg><div><small>Garages</small><b>01</b></div></div>
      </div>
    </article>
    <div class="photo" role="img" aria-label="Photo of a beige suburban house with porch" style="background:linear-gradient(180deg,#a3c0dc,#b9a783 50%,#5d7b35)"></div>
  </div>
</section>
<div class="grid-arrow" style="left:45px"><svg width="8" height="10"><path d="M6 1 L2 5 L6 9" stroke="#333" stroke-width="2" fill="none"/></svg></div>
<div class="grid-arrow" style="left:1130px"><svg width="8" height="10"><path d="M2 1 L6 5 L2 9" stroke="#333" stroke-width="2" fill="none"/></svg></div>

<section class="info buyer" role="img" aria-label="Teal-tinted photo of a smiling couple holding keys">
  <h2>Buyer Info</h2>
  <div class="copy">
    <p>Lorem Ipsum is simply dummy text of the printing and typesetting industry. Lorem Ipsum has been the industry's standard dummy text ever since the 1500s, when an unknown printer took a galley of type and scrambled it to make a type specimen book.</p>
    <p>It has survived not only five centuries, but also the leap into electronic typesetting, remaining essentially unchanged. It was popularised in the 1960s with the release of transfer sheets containing.</p>
  </div>
  <div class="btn"><span class="lbl">Learn More</span><span class="arr"><svg width="8" height="10"><path d="M2 1 L6 5 L2 9" stroke="#fff" stroke-width="2" fill="none"/></svg></span></div>
</section>
<section class="info seller" role="img" aria-label="Green-tinted photo of a happy couple in their home">
  <h2>Seller Info</h2>
  <div class="copy">
    <p>Lorem Ipsum is simply dummy text of the printing and typesetting industry. Lorem Ipsum has been the industry's standard dummy text ever since the 1500s, when an unknown printer took a galley of type and scrambled it to make a type specimen book.</p>
    <p>It has survived not only five centuries, but also the leap into electronic typesetting, remaining essentially unchanged. It was popularised in the 1960s with the release of transfer sheets containing.</p>
  </div>
  <div class="btn"><span class="lbl">Learn More</span><span class="arr"><svg width="8" height="10"><path d="M2 1 L6 5 L2 9" stroke="#fff" stroke-width="2" fill="none"/></svg></span></div>
</section>

<section class="clients">
  <h2 class="section-title">What Our Clients Say</h2>
  <span class="qmark" style="left:113px;top:112px">&ldquo;</span>
  <div class="avatar" role="img" aria-label="Portrait photo of the client"></div>
  <div class="divider"></div>
  <p class="quote-text">Lorem Ipsum is simply dummy text of the printing and typesetting industry. Lorem Ipsum has been the industry's standard dummy text ever since the 1500s, when an unknown printer took a galley of type and scrambled it to make a type specimen book. It has survived not only five centuries...</p>
  <div class="client-name">Marcus Ellery</div>
  <span class="qmark" style="left:1052px;top:178px">&rdquo;</span>
  <div class="dots"><span class="on"></span><span></span><span></span></div>
</section>

<section class="news">
  <h2 class="section-title">Latest News</h2>
  <div class="sub">Fresh news and Blog from the world of information</div>
  <article class="post" style="left:117px">
    <div class="thumb" role="img" aria-label="Photo of a bright living room interior" style="background:linear-gradient(135deg,#f1eee8,#b9aa95 60%,#6e5a44)"></div>
    <div class="body">
      <h4>Lorem Ipsum is simply dummy text of the and typesetting industry.</h4>
      <time>October 06. 2015</time>
      <p>Lorem Ipsum has been the industry's standard dummy text ever since the 1500s, when an unknown in printer took a galley of type...</p>
      <div class="more"><svg width="11" height="11"><circle cx="5.5" cy="5.5" r="4.5" fill="none" stroke="#8dc63f"/><path d="M4.5 3.5 L6.5 5.5 L4.5 7.5" stroke="#8dc63f" fill="none"/></svg>Read More</div>
    </div>
  </article>
  <article class="post" style="left:620px">
    <div class="thumb" role="img" aria-label="Photo of a hand holding keys with a small house model" style="background:linear-gradient(135deg,#f2f2f2,#d7c6b8 55%,#b94a3b)"></div>
    <div class="body">
      <h4>Lorem Ipsum is simply dummy text of the and typesetting industry.</h4>
      <time>October 06. 2015</time>
      <p>Lorem Ipsum has been the industry's standard dummy text ever since the 1500s, when an unknown in printer took a galley of type...</p>
      <div class="more"><svg width="11" height="11"><circle cx="5.5" cy="5.5" r="4.5" fill="none" stroke="#8dc63f"/><path d="M4.5 3.5 L6.5 5.5 L4.5 7.5" stroke="#8dc63f" fill="none"/></svg>Read More</div>
    </div>
  </article>
  <div class="btn"><span class="lbl">View More</span><span class="arr"><svg width="8" height="10"><path d="M2 1 L6 5 L2 9" stroke="#fff" stroke-width="2" fill="none"/></svg></span></div>
</section>

<footer class="footer">
  <div class="fcol" style="left:117px">
    <h5>Site Map</h5>
    <ul><li>- About Us</li><li>- Property</li><li>- Buyer Info</li><li>- Seller Info</li><li>- News</li><li>- Contact Us</li></ul>
  </div>
  <div class="fcol" style="left:286px;width:200px">
    <h5>Newsletter</h5>
    <div>Simply dummy text of the printing<br>and typesetting industry.</div>
    <div class="email-box">Enter Email</div>
    <div class="submit">SUBMIT</div>
  </div>
  <div class="fcol" style="left:545px;width:220px">
    <h5>Contact Detail</h5>
    <div style="font-weight:700;color:#fff">LANTERN DWELLING</div>
    <div>48 Harbor Lane, Westvale,<br>United States</div>
    <div style="margin-top:8px">Phone : (555) 014 2280</div>
    <div style="margin-top:8px">Email : hello@lanterndwelling.example</div>
  </div>
  <div class="map" role="img" aria-label="Street map showing the office location"></div>
  <div class="map-link">View Larger Map</div>
</footer>
<div class="base">
  <div class="links">Terms of Use &nbsp;|&nbsp; Privacy</div>
  <div class="copy">Copyright © 2016 - Lantern Dwelling Partners &nbsp;|&nbsp; All Rights Reserved.</div>
  <div class="social"><span></span><span></span><span></span><span></span></div>
</div>

</body>
</html>
```